Kesso Tea Premium Matcha brand Label

This is a label design project for a luxury tea brand. Feel free to be creative within the guidelines.
Attached to this project is a document called “Private Label Design Requirements” with the design guidelines and template. There is another document called "Kesso Tea Packaging Instructions" this has more details necessary to stick to the guidelines in the first document.

I have also attached the certifications to be included as well as different variations of the logo for you to use.

If you have any questions, I am here.
Updates

Need extra days to review

Target Market(s)

Young, active, fun, enjoy the finer things

```html
<!DOCTYPE html>
<html lang="en">
<head>
<meta charset="UTF-8">
<title>Kesso Tea – Premium Organic Ceremonial Matcha Label</title>
<link rel="stylesheet" href="https://fonts.googleapis.com/css2?family=Raleway:wght@500;600;700;800&display=swap">
<style>
  :root {
    --page-bg: #bfcab9;
    --label-bg: #2f3b33;
    --leaf-tone: #3a483e;
    --cream: #fbf1dc;
    --frame-green: #4f7a5e;
    --ink: #1f2420;
    --white: #ffffff;
    --badge-green: #2f7a45;
    --badge-blue: #3f8fc4;
  }
  * { margin: 0; padding: 0; box-sizing: border-box; }
  html, body {
    width: 1200px;
    height: 803px;
    overflow: hidden;
    background: var(--page-bg);
    font-family: "Raleway", sans-serif;
  }
  .canvas {
    position: relative;
    width: 1200px;
    height: 803px;
  }
  .label {
    position: absolute;
    left: 51px;
    top: 294px;
    width: 1098px;
    height: 213px;
    background: var(--label-bg);
    overflow: hidden;
  }
  .leaf-pattern {
    position: absolute;
    inset: 0;
    background: radial-gradient(ellipse at 30% 60%, var(--leaf-tone) 0%, var(--label-bg) 55%),
                radial-gradient(ellipse at 75% 40%, var(--leaf-tone) 0%, transparent 50%);
    background-blend-mode: lighten;
  }
  .distributor-info {
    position: absolute;
    left: 77px;
    top: 85px;
    color: var(--white);
    font-size: 10px;
    font-weight: 700;
    line-height: 16px;
  }
  .distributor-info .origin { font-weight: 600; }
  .title-badge {
    position: absolute;
    left: 442px;
    top: 28px;
    width: 216px;
    height: 156px;
  }
  .title-badge svg { position: absolute; inset: 0; }
  .badge-text {
    position: absolute;
    inset: 0;
    text-align: center;
    color: var(--ink);
  }
  .brand-name {
    position: absolute;
    top: 59px;
    width: 100%;
    font-size: 11px;
    font-weight: 800;
    display: flex;
    align-items: center;
    justify-content: center;
    gap: 4px;
  }
  .brand-name .mark {
    width: 7px;
    height: 7px;
    border-radius: 50%;
    background: var(--frame-green);
  }
  .product-name {
    position: absolute;
    top: 80px;
    width: 100%;
    font-size: 11.5px;
    font-weight: 800;
    line-height: 16px;
    letter-spacing: 0.2px;
  }
  .net-weight {
    position: absolute;
    top: 121px;
    width: 100%;
    font-size: 7px;
    font-weight: 700;
  }
  .product-details {
    position: absolute;
    left: 781px;
    top: 40px;
    color: var(--white);
  }
  .details-heading {
    font-size: 12px;
    font-weight: 600;
    line-height: 14px;
  }
  .ingredient-list {
    margin: 3px 0 0 8px;
    font-size: 10px;
    font-weight: 700;
    line-height: 13px;
  }
  .details-heading.instructions { margin-top: 10px; }
  .instruction-list {
    list-style: none;
    margin: 1px 0 0 8px;
    font-size: 9.5px;
    font-weight: 700;
    line-height: 12px;
  }
  .instruction-list li::before { content: "• "; }
  .certifications {
    position: absolute;
    left: 918px;
    top: 141px;
    display: flex;
    align-items: center;
    gap: 5px;
  }
  .cert-round {
    width: 32px;
    height: 32px;
    border-radius: 50%;
    background: var(--white);
    border: 5px solid var(--badge-green);
  }
  .cert-square {
    width: 35px;
    height: 26px;
    background: var(--badge-blue);
    border: 2px solid var(--white);
  }
</style>
</head>
<body>
<main class="canvas">
  <section class="label">
    <div class="leaf-pattern" role="img" aria-label="Background pattern of tea leaves in muted dark green"></div>

    <div class="distributor-info">
      <p>Distributed by Kesso Tea Co. | Atlanta, Ga</p>
      <p>Certified Organic by Verdant Cert</p>
      <p class="origin">PRODUCT OF JAPAN</p>
    </div>

    <div class="title-badge">
      <svg width="216" height="156" viewBox="0 0 216 156" aria-hidden="true">
        <rect x="2" y="2" width="212" height="152" rx="70" ry="70" fill="var(--cream)"/>
        <rect x="9" y="9" width="198" height="138" rx="63" ry="63" fill="none" stroke="var(--frame-green)" stroke-width="2"/>
        <rect x="13" y="13" width="190" height="130" rx="59" ry="59" fill="none" stroke="var(--frame-green)" stroke-width="0.8"/>
      </svg>
      <div class="badge-text">
        <p class="brand-name"><span class="mark"></span>Kesso Tea</p>
        <h1 class="product-name">PREMIUM ORGANIC<br>CEREMONIAL MATCHA</h1>
        <p class="net-weight">Net Wt: 30g</p>
      </div>
    </div>

    <div class="product-details">
      <h2 class="details-heading">Ingredients</h2>
      <p class="ingredient-list">Premium Organic Japanese Matcha Green Tea</p>
      <h2 class="details-heading instructions">Instructions</h2>
      <ul class="instruction-list">
        <li>2 tsp of Matcha</li>
        <li>2oz of Water (170-180 degrees F)</li>
        <li>Whisk in a W formation until frothy</li>
        <li>Sweeten to taste</li>
      </ul>
    </div>

    <div class="certifications">
      <span class="cert-round" aria-label="Organic certification badge"></span>
      <span class="cert-square" aria-label="Non-GMO verification badge"></span>
    </div>
  </section>
</main>
</body>
</html>
```